Business Card Design

Company is a Commercial Building Company specialising in New Construction and existing refurbishments

Industry/Entity Type

Business

Contact Information for Business Card

Liam Porter
Construction Manager
E Liam@marshbuilding.com.au
M 0400 213 594
Mail 14 Tarrant Rise Kestrel Bay WA 6299

```html
<!DOCTYPE html>
<html lang="en">
<head>
<meta charset="utf-8">
<title>Marsh Building &amp; Construction – Business Card</title>
<link href="https://fonts.googleapis.com/css2?family=Arimo:wght@400;700&display=swap" rel="stylesheet">
<style>
  :root {
    --backdrop: #2a2b2e;
    --card: #f7fafb;
    --ink: #1b1b1f;
    --brand-ink: #1f2b3d;
    --brand-blue: #1fb0dc;
    --skyline-dark: #1c1a20;
    --skyline-light: #cfcfcf;
  }
  * { box-sizing: border-box; margin: 0; padding: 0; }
  html, body {
    width: 1200px; height: 960px; overflow: hidden;
    background: var(--backdrop);
    font-family: "Arimo", Arial, sans-serif;
  }
  .stage { position: relative; width: 1200px; height: 960px; }
  .card {
    position: absolute;
    width: 540px; height: 320px;
    background: var(--card);
    border-radius: 3px;
    overflow: hidden;
    box-shadow: 0 10px 30px rgba(0,0,0,.45);
  }
  .card--front { left: 60px; top: 120px; }
  .card--back  { left: 600px; top: 500px; }

  .brand {
    position: absolute;
    display: flex; align-items: center; gap: 12px;
  }
  .brand__mark {
    width: 22px; height: 22px; background: var(--brand-blue); flex: none;
  }
  .brand__name {
    font-weight: 700; font-size: 19px; line-height: 1.15;
    color: var(--brand-ink); letter-spacing: .02em;
    text-transform: uppercase;
  }
  .card--front .brand { left: 40px; top: 150px; }
  .card--back .brand  { left: 30px; top: 145px; }

  .skyline { position: absolute; }
  .card--front .skyline {
    right: 0; bottom: 0; width: 250px; height: 230px;
    background: linear-gradient(180deg, #2a2830 0%, var(--skyline-dark) 100%);
  }
  .card--back .skyline {
    right: 0; bottom: 0; width: 270px; height: 200px;
    background: linear-gradient(180deg, #dadada 0%, var(--skyline-light) 100%);
  }

  .person {
    position: absolute; right: 30px; top: 30px; text-align: right; color: var(--ink);
  }
  .person__name { font-size: 22px; }
  .person__role { font-size: 13px; margin-top: 4px; }

  .contact {
    position: absolute; right: 30px; bottom: 30px; text-align: right;
    color: var(--ink); font-size: 14px; line-height: 1.55;
  }
</style>
</head>
<body>
<main class="stage">
  <section class="card card--front" aria-label="Business card front">
    <div class="brand">
      <span class="brand__mark"></span>
      <span class="brand__name">Marsh Building<br>&amp; Construction</span>
    </div>
    <div class="skyline" role="img" aria-label="Dark city skyline silhouette"></div>
  </section>

  <section class="card card--back" aria-label="Business card back">
    <div class="skyline" role="img" aria-label="Light grey city skyline silhouette"></div>
    <div class="brand">
      <span class="brand__mark"></span>
      <span class="brand__name">Marsh Building<br>&amp; Construction</span>
    </div>
    <div class="person">
      <p class="person__name">Liam Porter</p>
      <p class="person__role">Construction Manager</p>
    </div>
    <div class="contact">
      <p>0400 213 594</p>
      <p>Liam@marshbuilding.com.au</p>
      <p>14 Tarrant Rise Kestrel Bay WA 6299</p>
    </div>
  </section>
</main>
</body>
</html>
```